Design a New Business Card for Our Company

We are looking for fresh, unique, and a modern business card that reflects our roots as digital marketing agency focused on SEM.

Industry/Entity Type

Marketing

Contact Information for Business Card

looking for very unique out of the box designs. clean and modern that compliments our logo

Requirements
Must have
• colors should match our logo
• Front should have name, address, email, and phone/fax of the person, phone/fax are the same number
• back should have our url

```html
<!DOCTYPE html>
<html lang="en">
<head>
<meta charset="utf-8">
<title>Brightpath Media – Business Card</title>
<link rel="stylesheet" href="https://fonts.googleapis.com/css2?family=Source+Sans+3:wght@400;600;700&display=swap">
<style>
  :root {
    --backdrop: #3b3b3b;
    --card: #ffffff;
    --grey: #9a9a9a;
    --grey-text: #4a4a4a;
    --blue: #5b96d2;
    --circle-grey: #b3b3b3;
  }
  * { box-sizing: border-box; margin: 0; padding: 0; }
  html, body {
    width: 1105px;
    height: 1200px;
    overflow: hidden;
  }
  body {
    background: var(--backdrop);
    font-family: "Source Sans 3", sans-serif;
    position: relative;
  }
  .card {
    position: absolute;
    left: 196px;
    width: 720px;
    height: 412px;
    background: var(--card);
  }
  .card--front { top: 146px; }
  .card--back { top: 602px; }

  /* Front */
  .brand-name {
    position: absolute;
    left: 46px;
    top: 50px;
    font-size: 44px;
    font-weight: 700;
    color: var(--grey);
    letter-spacing: -0.5px;
    line-height: 1;
  }
  .person-name {
    position: absolute;
    left: 46px;
    top: 158px;
    font-size: 26px;
    font-weight: 600;
    color: var(--grey);
  }
  .person-title {
    position: absolute;
    left: 46px;
    top: 192px;
    font-size: 21px;
    color: var(--blue);
  }
  .address {
    position: absolute;
    left: 46px;
    top: 230px;
    font-size: 19px;
    line-height: 26px;
    color: var(--grey-text);
    font-style: normal;
  }
  .contact-list {
    position: absolute;
    left: 46px;
    top: 292px;
    list-style: none;
    font-size: 19px;
    line-height: 27.5px;
    color: var(--grey-text);
  }
  .contact-list li {
    display: flex;
    align-items: center;
    gap: 10px;
  }
  .contact-icon {
    width: 18px;
    height: 18px;
    fill: var(--circle-grey);
    flex: none;
  }
  .accent-circle {
    position: absolute;
    left: 454px;
    top: 106px;
    width: 200px;
    height: 200px;
    border-radius: 50%;
    background: var(--blue);
  }

  /* Back */
  .back-brand {
    position: absolute;
    left: 0;
    right: 0;
    top: 180px;
    display: flex;
    justify-content: center;
    align-items: center;
    gap: 18px;
  }
  .back-brand__dot {
    width: 46px;
    height: 46px;
    border-radius: 50%;
    background: var(--blue);
  }
  .back-brand__name {
    font-size: 50px;
    font-weight: 700;
    color: var(--grey);
    letter-spacing: -0.5px;
    line-height: 1;
  }
  .website {
    position: absolute;
    left: 0;
    right: 0;
    top: 348px;
    text-align: center;
    font-size: 18px;
    letter-spacing: 3px;
    color: var(--grey-text);
  }
</style>
</head>
<body>

<section class="card card--front" aria-label="Business card front">
  <div class="brand-name">Brightpath Media</div>
  <div class="person-name">Daniel Reyes</div>
  <div class="person-title">CEO/Founder</div>
  <address class="address">
    2140 Maple Ridge Road<br>
    Juneau, Alaska 99801
  </address>
  <ul class="contact-list">
    <li>
      <svg class="contact-icon" viewBox="0 0 24 24" aria-label="Phone">
        <path d="M6.6 10.8a15.1 15.1 0 0 0 6.6 6.6l2.2-2.2a1 1 0 0 1 1-.25 11.4 11.4 0 0 0 3.6.57 1 1 0 0 1 1 1V20a1 1 0 0 1-1 1A17 17 0 0 1 3 4a1 1 0 0 1 1-1h3.5a1 1 0 0 1 1 1c0 1.25.2 2.45.57 3.6a1 1 0 0 1-.25 1z"/>
      </svg>
      <span>555 210 4837</span>
    </li>
    <li>
      <svg class="contact-icon" viewBox="0 0 24 24" aria-label="Fax">
        <path d="M7 3h10v5H7z"/>
        <path d="M3 9h18v8h-3v-3H6v3H3z"/>
        <path d="M7 15h10v6H7z"/>
      </svg>
      <span>555 210 4838</span>
    </li>
    <li>
      <svg class="contact-icon" viewBox="0 0 24 24" aria-label="Email">
        <path d="M3 6h18v12H3z" />
        <path d="M3 6l9 7 9-7" fill="none" stroke="#fff" stroke-width="1.6"/>
      </svg>
      <span>hello@brightpathmedia.com</span>
    </li>
  </ul>
  <div class="accent-circle"></div>
</section>

<section class="card card--back" aria-label="Business card back">
  <div class="back-brand">
    <span class="back-brand__dot"></span>
    <span class="back-brand__name">Brightpath Media</span>
  </div>
  <div class="website">www.brightpathmedia.com</div>
</section>

</body>
</html>
```